Stationery Design Project for Nimbora, Chicago

Nimbora, a street parking application which helps car drivers find a street parking spot by offering an ideal path along which to look for parking. This path is calculated by our algorithm based on data (e.g. historical data, baseball games schedule, etc.). Along this path the driver will find a spot and will also save 70% of the search time. Customer we target is reg. between 21 and 45 yo.

We envision something young, fresh, bright and original. Slightly abstract maybe. It should represent the idea and elements of finding street parking in the city, e.g. car(s), parking spot, people, city, etc. (just ideas!).

Logo is attached.

Requirement:
- Business Cards (2 Sided Full Color CMYK)
- Letterhead (1 Sided Full Color CMYK)
- Envelope (1 Sided Full Color CMYK)
- Sticker (1 Sided Full Color CMYK), round with a 2inch diameter.

Reason: We're starting to get more and more designs and need more time to look into all of them. Very exciting!! Thanks to everybody!

Hi all, we're in the process of selecting our favs. Though choices!!! Really good submissions. Will keep you posted and sorry for the delay.

Target Market(s)

Car drivers and owners between 21 and 45

Industry/Entity Type

Parking

Requirements
Must have
• Sticker should be round and include company URL nimbora.com and the new logo which we will attach soon.
Should not have
• Should not be too serious or boring.

```html
<!DOCTYPE html>
<html lang="en">
<head>
<meta charset="utf-8">
<title>Nimbora – Business Card</title>
<link rel="stylesheet" href="https://fonts.googleapis.com/css2?family=Source+Sans+3:wght@400;600;700&display=swap">
<style>
  :root {
    --page-bg: #e6e6e6;
    --card-bg: #ffffff;
    --ink: #1a1a1a;
    --brand-blue: #2357a8;
    --wave-light: #1f73bb;
    --wave-dark: #2b3891;
    --swoosh: #1b1b1b;
    --on-blue: #ffffff;
  }
  * { margin: 0; padding: 0; box-sizing: border-box; }
  html, body { width: 954px; height: 1200px; overflow: hidden; }
  body {
    background: var(--page-bg);
    font-family: "Source Sans 3", "Myriad Pro", Arial, sans-serif;
    color: var(--ink);
    position: relative;
  }
  .card {
    position: absolute;
    left: 62px;
    width: 796px;
    height: 452px;
    background: var(--card-bg);
    border-radius: 28px;
    overflow: hidden;
    box-shadow: 0 4px 14px rgba(0,0,0,0.25);
  }
  .card--front { top: 100px; }
  .card--back { top: 648px; height: 454px; }
  .card__wave { position: absolute; inset: 0; width: 100%; height: 100%; }
  .brand { position: absolute; display: flex; align-items: center; }
  .brand__dot {
    border-radius: 50%;
    background: var(--brand-blue);
    flex: none;
  }
  .brand__name {
    font-weight: 600;
    color: var(--ink);
    line-height: 1;
    letter-spacing: 1px;
  }
  .card--front .brand { left: 104px; top: 54px; }
  .card--front .brand__dot { width: 156px; height: 156px; margin-right: 30px; }
  .card--front .brand__name { font-size: 104px; }
  .card--back .brand { left: 88px; top: 115px; }
  .card--back .brand__dot { width: 164px; height: 164px; margin-right: 30px; }
  .card--back .brand__name { font-size: 112px; }
  .holder {
    position: absolute; top: 222px; left: 0; width: 818px;
    text-align: center; font-size: 29px; font-weight: 700; line-height: 40px;
  }
  .contacts {
    position: absolute; top: 282px; left: 0; width: 818px;
    text-align: center; font-size: 21px; line-height: 27px;
  }
  .contacts b { font-weight: 700; }
  .contacts .sep { margin: 0 6px; color: var(--ink); }
  .address {
    position: absolute; top: 404px; left: 0; width: 790px;
    text-align: center; font-size: 21.5px; line-height: 28px; color: var(--on-blue);
  }
</style>
</head>
<body>
  <section class="card card--front">
    <svg class="card__wave" viewBox="0 0 796 452" aria-hidden="true">
      <defs>
        <linearGradient id="waveFront" x1="0" x2="1" y1="0" y2="0">
          <stop offset="0" stop-color="var(--wave-light)"/>
          <stop offset="1" stop-color="var(--wave-dark)"/>
        </linearGradient>
      </defs>
      <path d="M528 367 C650 360 740 320 796 242 L796 290 C740 330 650 362 528 367 Z" fill="var(--swoosh)"/>
      <path d="M0 395 C60 360 150 350 300 358 C420 366 480 372 560 368 C650 362 740 335 796 300 L796 452 L0 452 Z" fill="url(#waveFront)"/>
    </svg>
    <div class="brand">
      <span class="brand__dot"></span>
      <span class="brand__name">nimbora</span>
    </div>
    <p class="holder">Your Name - Designation</p>
    <p class="contacts">
      <b>t</b> : 123-456-7890 <span class="sep">|</span> <b>m</b> : 123-456-7890<br>
      <b>e</b> : name@nimbora.com <span class="sep">|</span> <b>w</b> : www.nimbora.com
    </p>
    <p class="address">Street Name, City Name, State Name, Country Code</p>
  </section>

  <section class="card card--back">
    <svg class="card__wave" viewBox="0 0 796 454" aria-hidden="true">
      <defs>
        <linearGradient id="waveBack" x1="0" x2="1" y1="0" y2="0">
          <stop offset="0" stop-color="var(--wave-light)"/>
          <stop offset="1" stop-color="var(--wave-dark)"/>
        </linearGradient>
      </defs>
      <path d="M528 370 C650 362 740 322 796 244 L796 292 C740 332 650 364 528 370 Z" fill="var(--swoosh)"/>
      <path d="M0 398 C60 362 150 352 300 360 C420 368 480 374 560 370 C650 364 740 338 796 302 L796 454 L0 454 Z" fill="url(#waveBack)"/>
    </svg>
    <div class="brand">
      <span class="brand__dot"></span>
      <span class="brand__name">nimbora</span>
    </div>
  </section>
</body>
</html>
```